Business Card Re-Design/Update

We'd like to update out business cards. I've included our current "Style guide" which has the colour scheme of the organisation in it. I've also included the branding files with logos etc in them.

I've also included a copy of one of our existing cards so that you can see how ugly/dated they look. I'd like a fresh modern corporate look.

Target Market(s)

These are for our clients, potential clients, industry contacts - like all business cards

Contact Information for Business Card

Name
Position
Company Address - Level 1, 47 Fernby Street, Carlow Qld 4072
Direct Phone
mobile
Email
Website -www.korvalit.com.au
Logo

Colors

Designer to choose colors to be used in the design.

Requirements
Must have
• Main Logo
• Cards will need to be editable to be able to personalize them for each new employee.
Nice to have
• The MapOut, ShipWell, KeepSteady would be okay to have if they can be sensibly and professionally added to the look without detracting from the main imagery.
• Maybe they could go on the back of the card? will leave this to your creative discretion as to whether/where they fit.
Should not have
• Should not have decorative or script fonts

```html
<!DOCTYPE html>
<html lang="en">
<head>
<meta charset="utf-8">
<title>korvalIT Business Card</title>
<link href="https://fonts.googleapis.com/css2?family=Asap:wght@400;500;600&family=Asap+Condensed:wght@600&display=swap" rel="stylesheet">
<style>
  :root {
    --backdrop: #e4e2df;
    --card-front: #f4f4f4;
    --card-back: #1b1c1e;
    --brand-red: #c4161c;
    --band-red: #c0202a;
    --ink: #1e1e1e;
    --ink-soft: #5a5a5a;
    --divider: #c9c9c9;
    --plan-green: #5a9e35;
    --deliver-blue: #1b8ad3;
    --sustain-magenta: #bb1d8f;
  }
  * { box-sizing: border-box; margin: 0; padding: 0; }
  html, body {
    width: 1200px; height: 960px; overflow: hidden;
    background: var(--backdrop);
    font-family: "Asap", Arial, sans-serif;
  }
  .stage { position: relative; width: 1200px; height: 960px; }

  .card {
    position: absolute; width: 600px; height: 342px;
    box-shadow: 0 3px 8px rgba(0,0,0,.25);
  }
  .card-front { left: 314px; top: 113px; background: var(--card-front); }
  .card-back  { left: 311px; top: 472px; background: var(--card-back); }

  .front-band {
    position: absolute; left: 0; bottom: 0; width: 100%; height: 15px;
    background: var(--band-red);
  }

  .brand {
    position: absolute; left: 42px; top: 151px;
    display: flex; align-items: center; gap: 12px;
  }
  .brand-square { width: 26px; height: 26px; background: var(--brand-red); }
  .brand-name {
    font-weight: 500; font-size: 33px; color: var(--ink); letter-spacing: -0.5px;
  }

  .divider {
    position: absolute; left: 300px; top: 70px; width: 1px; height: 205px;
    background: var(--divider);
  }

  .details { position: absolute; left: 327px; top: 64px; color: var(--ink-soft); }
  .person-name {
    font-family: "Asap Condensed", "Arial Narrow", sans-serif;
    font-weight: 600; font-size: 21px; color: var(--brand-red); line-height: 24px;
  }
  .person-role { font-size: 15px; color: var(--ink); line-height: 20px; margin-bottom: 11px; }
  .address { font-size: 14px; line-height: 18px; margin-bottom: 9px; }
  .contact-list { list-style: none; font-size: 14px; }
  .contact-list li { display: flex; align-items: center; height: 19px; }
  .contact-list svg { width: 13px; height: 13px; margin-right: 12px; fill: var(--brand-red); flex: none; }

  .back-name {
    position: absolute; left: 0; top: 112px; width: 100%; text-align: center;
    font-weight: 600; font-size: 64px; color: var(--brand-red); letter-spacing: -1px;
  }
  .services {
    position: absolute; left: 0; top: 276px; width: 100%;
    display: flex; justify-content: center; gap: 40px;
  }
  .service { display: flex; align-items: center; gap: 8px; font-weight: 600; font-size: 24px; }
  .service-dot { width: 18px; height: 18px; border-radius: 50%; }
  .service-map { color: var(--plan-green); }
  .service-map .service-dot { background: var(--plan-green); }
  .service-ship { color: var(--deliver-blue); }
  .service-ship .service-dot { background: var(--deliver-blue); }
  .service-keep { color: var(--sustain-magenta); }
  .service-keep .service-dot { background: var(--sustain-magenta); }
</style>
</head>
<body>
<main class="stage">

  <section class="card card-front">
    <div class="brand">
      <span class="brand-square"></span>
      <span class="brand-name">korvalIT</span>
    </div>

    <div class="divider"></div>

    <div class="details">
      <p class="person-name">Mara Ellison</p>
      <p class="person-role">Business Development Manager</p>
      <p class="address">47 Fernby Street<br>Carlow QLD 4072</p>
      <ul class="contact-list">
        <li><svg viewBox="0 0 16 16" aria-hidden="true"><path d="M3 1l3 3-2 2c1 2 4 5 6 6l2-2 3 3-2 2C7 15 1 9 1 3z"/></svg>+61 (0)7 5550 2140</li>
        <li><svg viewBox="0 0 16 16" aria-hidden="true"><path d="M3 1l3 3-2 2c1 2 4 5 6 6l2-2 3 3-2 2C7 15 1 9 1 3z"/></svg>+61 (0)7 5550 2157</li>
        <li><svg viewBox="0 0 16 16" aria-hidden="true"><path d="M4 0h8v16H4zM5.5 2v10h5V2z"/></svg>+61 (0)491 570 318</li>
        <li><svg viewBox="0 0 16 16" aria-hidden="true"><path d="M4 1h8v4H4zM1 6h14v7H1zM4 11h8v4H4z"/></svg>+61 (0)7 5550 2199</li>
        <li><svg viewBox="0 0 16 16" aria-hidden="true"><path d="M1 3h14v10H1zM1 4l7 5 7-5v-1H1z"/></svg>mellison@korvalit.com.au</li>
        <li><svg viewBox="0 0 16 16" aria-hidden="true"><circle cx="8" cy="8" r="7"/></svg>www.korvalit.com.au</li>
      </ul>
    </div>

    <div class="front-band"></div>
  </section>

  <section class="card card-back">
    <p class="back-name">korvalIT</p>
    <div class="services">
      <span class="service service-map"><span class="service-dot"></span>MapOut</span>
      <span class="service service-ship"><span class="service-dot"></span>ShipWell</span>
      <span class="service service-keep"><span class="service-dot"></span>KeepSteady</span>
    </div>
  </section>

</main>
</body>
</html>
```